Website Re-design for Kids Playhouse Business

Need current website which looks very outdated to be re-designed to look modern and contemporary, reduce clutter significantly and make it look elegant and simple.
Current website: http://www.tumblenest.com.au/
A website which the business owner likes, use as reference/inspiration: http://vexa.com.au/
Looking for light green palette, natural colours. "WHAT'S ON" page/link no longer required.
Industry/Entity Type
Business
Number of Pages Required
5+ page
Look and feel
Each slider illustrates characteristics of the customer's brand and the style your logo design should communicate.

```html
<!DOCTYPE html>
<html lang="en">
<head>
<meta charset="utf-8">
<title>Tumble Nest Playhouse &amp; Cafe</title>
<link href="https://fonts.googleapis.com/css2?family=Montserrat:wght@400;600;700&family=Open+Sans:wght@400;600&display=swap" rel="stylesheet">
<style>
:root{
  --page:#e7f1da;
  --panel:#f2f7ea;
  --ink:#2d2d2d;
  --muted:#6b6f66;
  --red:#d42a2f;
  --green:#8cc63f;
  --line:#c9d6b8;
  --white:#ffffff;
}
*{box-sizing:border-box;margin:0;padding:0}
html,body{width:1200px;height:2692px;overflow:hidden}
body{background:var(--page);color:var(--ink);font-family:"Open Sans",sans-serif;position:relative}
.abs{position:absolute}
h2.section-title{position:absolute;left:0;width:1200px;text-align:center;font-family:"Montserrat",sans-serif;font-weight:600;font-size:26px;color:var(--ink)}
.btn{display:inline-block;background:var(--red);color:var(--white);font-family:"Montserrat",sans-serif;font-weight:700;font-size:13px;letter-spacing:1px;padding:9px 16px;text-transform:uppercase}

/* hero */
.hero{left:0;top:0;width:1200px;height:672px;background:linear-gradient(160deg,#c9a87e 0%,#b98a5c 40%,#8f6b4a 70%,#5b4636 100%)}
.hero::after{content:"";position:absolute;inset:0;background:linear-gradient(180deg,rgba(0,0,0,.15),rgba(0,0,0,.05) 40%,rgba(0,0,0,.35))}
.brand{left:120px;top:40px;width:200px;height:96px;background:var(--white);display:flex;align-items:center;justify-content:center;gap:8px;z-index:2;border-radius:4px}
.brand-dot{width:14px;height:14px;border-radius:50%;background:var(--red)}
.brand-name{font-family:"Montserrat",sans-serif;font-weight:700;font-size:20px;color:var(--red);line-height:1.1}
.nav{left:420px;top:44px;width:620px;height:76px;background:rgba(255,255,255,.85);display:flex;z-index:2}
.nav a{flex:1;display:flex;align-items:center;justify-content:center;text-align:center;font-family:"Montserrat",sans-serif;font-size:12px;font-weight:600;color:var(--ink);text-decoration:none;padding:0 6px;line-height:1.3}
.nav a.active{background:var(--green);color:var(--white)}
.phone{left:1048px;top:20px;z-index:2;color:var(--white);font-family:"Montserrat",sans-serif}
.phone small{display:block;font-size:11px;opacity:.85}
.phone strong{font-size:18px}
.hero-title{left:0;top:380px;width:1200px;text-align:center;color:var(--white);font-family:"Montserrat",sans-serif;font-weight:700;font-size:60px;line-height:1.1;z-index:2;text-transform:uppercase;letter-spacing:1px}
.dots{display:flex;gap:10px;justify-content:center}
.dots i{width:10px;height:10px;border-radius:50%;background:rgba(255,255,255,.6);display:block}
.dots i.on{background:var(--white)}
.hero .dots{position:absolute;left:0;width:1200px;top:622px;z-index:2}

/* welcome */
.welcome-head{left:120px;top:750px;font-family:"Montserrat",sans-serif}
.welcome-head p{font-size:17px;font-weight:600}
.welcome-head h1{font-size:26px;font-weight:700;line-height:1.3;margin:12px 0 18px;text-transform:uppercase}
.divider{left:470px;top:740px;width:2px;height:200px;background:var(--line)}
.welcome-text{left:505px;top:748px;width:580px;font-size:15px;line-height:1.75;color:var(--muted)}

/* features */
.feature{width:340px;top:1108px}
.feature .photo{width:340px;height:314px}
.feature h3{font-family:"Montserrat",sans-serif;font-weight:400;font-size:18px;line-height:1.3;margin:18px 0 12px}

/* testimonials */
.quote{left:320px;top:1700px;width:560px;text-align:center;font-size:17px;line-height:1.8;color:var(--muted);font-style:italic}
.quote-mark{font-family:"Montserrat",sans-serif;font-size:90px;color:#b8c6a7;line-height:1}
.testimonial-dots{left:0;top:1858px;width:1200px}
.testimonial-dots i{background:#c9b8b8}
.testimonial-dots i.on{background:var(--red)}

/* gallery */
.gallery{left:16px;top:2030px;width:1168px;height:270px;display:flex;gap:16px}
.gallery div{flex:1}

/* footer */
.footer-brand{left:130px;top:2360px;width:210px;height:150px;background:var(--white);display:flex;align-items:center;justify-content:center;gap:8px;border-radius:4px}
.contact{left:420px;top:2350px;font-size:13px;color:var(--muted)}
.contact h4{font-family:"Montserrat",sans-serif;font-size:14px;color:var(--ink);margin-bottom:16px;text-transform:uppercase}
.contact li{list-style:none;display:flex;align-items:center;gap:10px;margin-bottom:14px}
.contact svg{flex:none}
.form{left:680px;top:2350px;width:392px;display:grid;grid-template-columns:1fr 1fr;gap:12px}
.field{background:var(--white);height:38px;font-size:12px;color:#9a9a9a;padding:11px 12px}
.field.message{grid-column:1/3;height:64px}
.form .btn{justify-self:start}
.footer-rule{left:60px;top:2590px;width:1080px;height:1px;background:var(--line)}
.follow{left:120px;top:2628px;display:flex;align-items:center;gap:12px;font-family:"Montserrat",sans-serif;font-weight:700;font-size:14px}
.follow span.circle{width:26px;height:26px;border-radius:50%;background:#3b6fb6;display:block}
.follow span.circle.alt{background:#38a7df}
.copyright{left:720px;top:2634px;width:400px;text-align:right;font-size:12px;color:var(--muted)}
</style>
</head>
<body>

<section class="hero abs" role="img" aria-label="Children in party hats celebrating a birthday around a table"></section>
<div class="brand abs"><span class="brand-dot"></span><span class="brand-name">Tumble Nest<br>Playhouse &amp; Cafe</span></div>
<nav class="nav abs">
  <a class="active" href="#">Home</a>
  <a href="#">Price &amp; Menu</a>
  <a href="#">Party Packages</a>
  <a href="#">Party Rooms</a>
  <a href="#">Opening Hours</a>
  <a href="#">School Holidays</a>
  <a href="#">Reviews &amp; Feedback</a>
</nav>
<div class="phone abs"><small>Call us today</small><strong>02 9000 4821</strong></div>
<h2 class="hero-title abs">So much<br>fun for everyone</h2>
<div class="hero"><div class="dots"><i></i><i class="on"></i><i></i><i></i><i></i></div></div>

<div class="welcome-head abs">
  <p>Welcome to</p>
  <h1>Tumble Nest<br>Playhouse &amp; Cafe</h1>
  <a class="btn" href="#">Read more</a>
</div>
<div class="divider abs"></div>
<p class="welcome-text abs">Tumble Nest is an indoor kids play centre and cafe that offers both kids and adults a chance to enjoy their time together. We take pride in offering the best indoor play centre for your kids to engage in fun and learning activities in a specially created environment that is not only warm and safe but also enhances and stimulates creativity and curiosity in a child. We also offer a variety of kids party venues like our themed party rooms.</p>

<h2 class="section-title" style="top:1010px">Our Features</h2>
<div class="feature abs" style="left:68px">
  <div class="photo" role="img" aria-label="Children gathered at a birthday party table" style="background:linear-gradient(150deg,#7a2a20,#c2432f 55%,#3b1712)"></div>
  <h3>Perfect venue for birthdays<br>and private parties</h3>
  <a class="btn" href="#">View parties</a>
</div>
<div class="feature abs" style="left:430px">
  <div class="photo" role="img" aria-label="Colourfully lit themed party room" style="background:linear-gradient(150deg,#2b1f4d,#6a3a8a 50%,#c06a3a)"></div>
  <h3>4 kids loving<br>party rooms themes</h3>
  <a class="btn" href="#">View party rooms</a>
</div>
<div class="feature abs" style="left:792px">
  <div class="photo" role="img" aria-label="Group of children enjoying a school holiday program" style="background:linear-gradient(150deg,#3f6a8a,#8fa3b8 50%,#b45a4a)"></div>
  <h3>We host school<br>holiday programs</h3>
  <a class="btn" href="#">View programs</a>
</div>

<h2 class="section-title" style="top:1632px">Testimonials</h2>
<div class="quote-mark abs" style="left:320px;top:1680px">&ldquo;</div>
<p class="quote abs">Had my son's birthday party there. Kids had such a great time! I recommend this place to everyone! Staff are amazing. Food and coffee are delicious! Thank you.</p>
<div class="quote-mark abs" style="left:840px;top:1740px">&rdquo;</div>
<div class="dots testimonial-dots abs"><i></i><i class="on"></i><i></i><i></i></div>

<h2 class="section-title" style="top:1950px">Gallery</h2>
<div class="gallery abs">
  <div role="img" aria-label="Child on a colourful slide" style="background:linear-gradient(160deg,#e0b13a,#5c8bd0 60%,#c2462f)"></div>
  <div role="img" aria-label="Children playing in a ball pit" style="background:linear-gradient(160deg,#3b7ac0,#d8d23a 50%,#c2462f)"></div>
  <div role="img" aria-label="Two children smiling at the play centre" style="background:linear-gradient(160deg,#6a3a2a,#c79a7a 55%,#8a4a3a)"></div>
  <div role="img" aria-label="Families seated in the cafe area" style="background:linear-gradient(160deg,#8a6a4a,#d0b890 55%,#6a4a3a)"></div>
</div>

<div class="footer-brand abs"><span class="brand-dot"></span><span class="brand-name">Tumble Nest<br>Playhouse &amp; Cafe</span></div>
<ul class="contact abs">
  <h4>Contact us</h4>
  <li><svg width="14" height="18" viewBox="0 0 14 18"><path d="M7 0a7 7 0 0 0-7 7c0 5 7 11 7 11s7-6 7-11a7 7 0 0 0-7-7zm0 10a3 3 0 1 1 0-6 3 3 0 0 1 0 6z" fill="#d42a2f"/></svg>14 Fernleaf Avenue,<br>Riverwood NSW 2210</li>
  <li><svg width="14" height="14" viewBox="0 0 14 14"><path d="M3 0l3 3-2 2a9 9 0 0 0 5 5l2-2 3 3-2 3C6 14 0 8 0 2z" fill="#d42a2f"/></svg>02 9000 4821</li>
  <li><svg width="16" height="12" viewBox="0 0 16 12"><rect width="16" height="12" rx="1" fill="#d42a2f"/><path d="M1 1l7 6 7-6" stroke="#fff" fill="none"/></svg>hello@tumblenest.com.au</li>
</ul>
<div class="form abs">
  <div class="field">Name</div>
  <div class="field">E-mail</div>
  <div class="field">Phone</div>
  <div class="field">Website</div>
  <div class="field message">Message</div>
  <a class="btn" href="#">Send message</a>
</div>
<div class="footer-rule abs"></div>
<div class="follow abs">FOLLOW US <span class="circle"></span><span class="circle alt"></span></div>
<p class="copyright abs">Copyright &copy; 2016 All Rights Reserved</p>

</body>
</html>
```